Chimney Service company needs new business card design

We need a updated business card with our new logo added. We provide a full range of chimney services throughout Vermont and New Hampshire. The business card will be one sided and color. Attached is our current business card another document showing all the information we would like on the card.
We dont like a lot of flashy colors.... here is a link to our website to get an idea of our branding www.flueguardianvt.example

Target Market(s)

homeowners

Industry/Entity Type

Business

Contact Information for Business Card

See attached sheet for content.

Font styles to use
Serif
Sans Serif

Requirements
Must have
• all information provided on separate sheet
Should not have
• Additional information that may clogg up design

```html
<!DOCTYPE html>
<html lang="en">
<head>
<meta charset="utf-8">
<title>Flue Guardian Business Card</title>
<link rel="stylesheet" href="https://fonts.googleapis.com/css2?family=Marcellus+SC&display=swap">
<style>
  :root {
    --bg: #e9e7e4;
    --card: #ffffff;
    --ink: #262626;
    --brand-red: #a10b10;
  }
  * { margin: 0; padding: 0; box-sizing: border-box; }
  html, body {
    width: 1200px; height: 1000px; overflow: hidden;
    background: var(--bg);
    font-family: "Marcellus SC", "Times New Roman", serif;
    color: var(--ink);
  }
  .card {
    position: absolute; left: 100px; top: 215px;
    width: 1000px; height: 570px;
    background: var(--card);
    border-radius: 34px;
    overflow: hidden;
    box-shadow: 0 6px 24px rgba(0,0,0,0.15);
  }
  .accent-bar { position: absolute; width: 34px; background: var(--brand-red); }
  .accent-bar--top { right: 0; top: 70px; height: 140px; }
  .accent-bar--bottom { left: 0; top: 330px; height: 150px; }

  .brand { position: absolute; left: 110px; top: 70px; display: flex; align-items: center; gap: 22px; }
  .brand-mark { width: 74px; height: 74px; background: var(--ink); }
  .brand-name { font-size: 54px; letter-spacing: 1px; color: var(--ink); line-height: 1; }
  .brand-tagline { position: absolute; left: 112px; top: 170px; font-size: 18px; letter-spacing: 0.5px; }

  .divider { position: absolute; left: 500px; top: 225px; width: 2px; height: 185px; background: var(--brand-red); }

  .contact { position: absolute; right: 525px; top: 300px; text-align: right; font-size: 21px; line-height: 32px; }
  .contact-row { display: flex; align-items: center; justify-content: flex-end; gap: 8px; }
  .contact-row svg { width: 18px; height: 18px; }

  .services { position: absolute; left: 525px; top: 222px; }
  .services-title { color: var(--brand-red); font-size: 30px; letter-spacing: 0.5px; margin-bottom: 6px; }
  .services-list { list-style: none; font-size: 21px; line-height: 29px; }
  .services-list li { display: flex; align-items: center; gap: 8px; }
  .services-list svg { width: 12px; height: 16px; }
  .services-note { color: var(--brand-red); font-size: 23px; margin-top: 8px; }

  .footer-line { position: absolute; left: 70px; top: 485px; font-size: 29px; color: var(--brand-red); display: flex; align-items: center; gap: 16px; }
  .footer-dot { width: 10px; height: 10px; border-radius: 50%; background: var(--ink); }
</style>
</head>
<body>
  <div class="card">
    <div class="accent-bar accent-bar--top"></div>
    <div class="accent-bar accent-bar--bottom"></div>

    <div class="brand">
      <div class="brand-mark"></div>
      <div class="brand-name">Flue Guardian</div>
    </div>
    <div class="brand-tagline">Serving VT and New Hampshire since 1989</div>

    <div class="contact">
      <div class="contact-row">802-555-0147
        <svg viewBox="0 0 20 20"><circle cx="10" cy="10" r="9" fill="var(--brand-red)"/><path d="M6 5l2 0 1 3-1.5 1a6 6 0 0 0 3.5 3.5l1-1.5 3 1 0 2c-5 1-10-4-9-9z" fill="#fff"/></svg>
      </div>
      <div class="contact-row">info@flueguardianvt.example
        <svg viewBox="0 0 20 20"><rect x="1" y="4" width="18" height="12" rx="1" fill="var(--brand-red)"/><path d="M2 5l8 6 8-6" stroke="#fff" stroke-width="1.5" fill="none"/></svg>
      </div>
      <div class="contact-row">www.flueguardianvt.example
        <svg viewBox="0 0 20 20"><circle cx="10" cy="10" r="9" fill="var(--brand-red)"/><g stroke="#fff" stroke-width="1.2" fill="none"><ellipse cx="10" cy="10" rx="4" ry="8"/><path d="M2 10h16M4 6h12M4 14h12"/></g></svg>
      </div>
    </div>

    <div class="divider"></div>

    <div class="services">
      <div class="services-title">Services we provide</div>
      <ul class="services-list">
        <li><svg viewBox="0 0 12 16"><path d="M6 0c1 4 6 6 5 11a5 5 0 0 1-10 0c0-3 2-4 2-6 1 2 2 2 2 2S4 3 6 0z" fill="var(--brand-red)"/></svg>Full Masonry Services</li>
        <li><svg viewBox="0 0 12 16"><path d="M6 0c1 4 6 6 5 11a5 5 0 0 1-10 0c0-3 2-4 2-6 1 2 2 2 2 2S4 3 6 0z" fill="var(--brand-red)"/></svg>Historic chimney restoration</li>
        <li><svg viewBox="0 0 12 16"><path d="M6 0c1 4 6 6 5 11a5 5 0 0 1-10 0c0-3 2-4 2-6 1 2 2 2 2 2S4 3 6 0z" fill="var(--brand-red)"/></svg>Stainless steel liners</li>
        <li><svg viewBox="0 0 12 16"><path d="M6 0c1 4 6 6 5 11a5 5 0 0 1-10 0c0-3 2-4 2-6 1 2 2 2 2 2S4 3 6 0z" fill="var(--brand-red)"/></svg>New Chimney Installations</li>
        <li><svg viewBox="0 0 12 16"><path d="M6 0c1 4 6 6 5 11a5 5 0 0 1-10 0c0-3 2-4 2-6 1 2 2 2 2 2S4 3 6 0z" fill="var(--brand-red)"/></svg>ICSG Certified Chimney sweeps</li>
      </ul>
      <div class="services-note">Family owned and operated</div>
    </div>

    <div class="footer-line">
      <span>Fully Insured – Free Estimates</span>
      <span class="footer-dot"></span>
      <span>Family owned and operated</span>
    </div>
  </div>
</body>
</html>
```